Designing a brochures for an educational counseling service provider

We would like a 4 sided design on a 11x8.5 paper, half folded. I have including a sample design we did to give you an idea of what we envision but we welcome creativity to make beautiful looking flyers. Text for the flier is included as well as our logo.
- The most important thing is capturing our audience/market. We will be handing these flies to schools, organizations and individual clients.

www.pvrlearningadvisors.example

Target Market(s)

We are targeting international students wanting to study in the U.S and Canada.

Industry/Entity Type

Education

Requirements
Must have
• - Clean and clear
• - Our logo should visible and well placed.
• - Could you the pictures of students, libraries and school buildings or you could use the pictures we already have.
Nice to have
• We would like this to match business cards.

```html
<!DOCTYPE html>
<html lang="en">
<head>
<meta charset="utf-8">
<title>PVR Learning Advisors – Brochure Covers</title>
<link href="https://fonts.googleapis.com/css2?family=Open+Sans:wght@400;600;700;800&display=swap" rel="stylesheet">
<style>
  :root {
    --backdrop: #e9e7e3;
    --navy: #1f2a7a;
    --royal: #1c4fa8;
    --sky: #2a7fd0;
    --green: #6cbf3c;
    --ink: #1d1d2b;
    --paper: #ffffff;
    --mist: #e6e8ec;
  }
  * { box-sizing: border-box; margin: 0; padding: 0; }
  html, body {
    width: 1200px; height: 900px; overflow: hidden;
    background: var(--backdrop);
    font-family: "Open Sans", Arial, sans-serif;
    color: var(--ink);
  }
  .spread {
    position: absolute; left: 95px; top: 60px;
    width: 1010px; height: 780px;
    display: flex;
    box-shadow: 0 10px 30px rgba(0,0,0,.18);
  }
  .page {
    position: relative; width: 505px; height: 780px; overflow: hidden;
    background: linear-gradient(180deg, var(--paper) 0%, var(--mist) 100%);
  }

  /* shared brand lockup */
  .brand { display: flex; align-items: center; gap: 10px; }
  .brand-dot { width: 38px; height: 38px; border-radius: 50%; background: var(--royal); flex: none; }
  .brand-name {
    font-weight: 800; font-size: 20px; line-height: 1.05; color: var(--royal);
    text-transform: uppercase; letter-spacing: .3px;
  }

  /* back cover */
  .back-photo {
    position: absolute; left: 0; top: 0; width: 505px; height: 415px;
    background: linear-gradient(180deg, #a9c6e6 0%, #3b3f5a 55%, #1e1c2c 100%);
  }
  .back .brand { position: absolute; left: 140px; top: 448px; }
  .contact {
    position: absolute; left: 60px; top: 515px; width: 385px;
    text-align: center; font-size: 10.5px; line-height: 1.55;
  }
  .contact-title { color: var(--green); font-weight: 700; font-size: 11px; }
  .contact-role { font-weight: 700; }
  .back-band {
    position: absolute; left: 0; bottom: 0; width: 505px; height: 48px;
    background: linear-gradient(90deg, var(--navy), var(--royal));
  }

  /* front cover */
  .front-photo {
    position: absolute; left: 0; top: 90px; width: 505px; height: 450px;
    background: linear-gradient(160deg, #8fbf6e 0%, #5d8f4a 35%, #c9b7a6 70%, #6d8fb8 100%);
  }
  .front-curve { position: absolute; left: 0; top: 0; }
  .front .brand { position: absolute; right: 28px; top: 58px; width: 200px; }
  .tagline {
    position: absolute; left: 0; top: 540px; width: 505px; height: 62px;
    background: var(--green); color: #fff;
    font-weight: 700; font-size: 15.5px; line-height: 1.3;
    display: flex; align-items: center; justify-content: center; text-align: center;
  }
  .services {
    position: absolute; left: 0; top: 602px; width: 505px; height: 138px;
    background: linear-gradient(90deg, var(--royal) 0%, var(--sky) 100%);
    display: flex; justify-content: space-around; align-items: center; padding: 0 10px;
  }
  .service { width: 110px; text-align: center; color: #fff; font-size: 11px; font-weight: 600; }
  .service-icon {
    width: 52px; height: 52px; margin: 0 auto 8px;
    border: 2px solid #fff; border-radius: 50%;
    display: flex; align-items: center; justify-content: center;
  }
  .front-strip {
    position: absolute; left: 0; bottom: 0; width: 505px; height: 32px;
    background: linear-gradient(90deg, var(--navy), var(--royal));
  }
</style>
</head>
<body>
<main class="spread">

  <section class="page back">
    <div class="back-photo" role="img" aria-label="Photo of smiling graduates in gowns tossing their caps against a blue sky"></div>
    <div class="brand">
      <span class="brand-dot"></span>
      <span class="brand-name">PVR Learning<br>Advisors</span>
    </div>
    <div class="contact">
      <p class="contact-title">CONTACT US</p>
      <p class="contact-role">Executive Director &amp; Independent Educational Consultant</p>
      <p>PVR Learning Advisors, LLC, 418 Cedar Ridge Rd, Suite 120, Maple Grove, TX 75010</p>
      <p>Phone: 555-014-2290</p>
      <p>Email: hello@pvrlearningadvisors.example</p>
    </div>
    <div class="back-band"></div>
  </section>

  <section class="page front">
    <div class="front-photo" role="img" aria-label="Photo of a group of smiling students holding notebooks outdoors"></div>
    <svg class="front-curve" width="505" height="540" viewBox="0 0 505 540" aria-hidden="true">
      <defs>
        <linearGradient id="top-fade" x1="0" y1="0" x2="0" y2="1">
          <stop offset="0" stop-color="#f3f4f6"/>
          <stop offset="1" stop-color="#ffffff"/>
        </linearGradient>
      </defs>
      <path d="M0,0 H505 V440 C465,300 370,160 190,92 L0,92 Z" fill="url(#top-fade)"/>
      <path d="M190,92 C370,160 465,300 505,440" fill="none" stroke="#1c4fa8" stroke-width="7"/>
    </svg>
    <div class="brand">
      <span class="brand-dot"></span>
      <span class="brand-name">PVR Learning<br>Advisors</span>
    </div>
    <p class="tagline">A full - service international educational consulting group<br>serving students and families across the globe</p>
    <div class="services">
      <div class="service">
        <div class="service-icon">
          <svg width="28" height="28" viewBox="0 0 28 28" fill="none" stroke="#fff" stroke-width="2">
            <path d="M3 10 L14 4 L25 10 Z"/><path d="M6 11v10M11 11v10M17 11v10M22 11v10M3 24h22"/>
          </svg>
        </div>Boarding Schools
      </div>
      <div class="service">
        <div class="service-icon">
          <svg width="28" height="28" viewBox="0 0 28 28" fill="none" stroke="#fff" stroke-width="2">
            <path d="M6 3h12l4 4v18H6Z"/><path d="M10 12h8M10 16h8M10 20h5"/>
          </svg>
        </div>College Admission
      </div>
      <div class="service">
        <div class="service-icon">
          <svg width="28" height="28" viewBox="0 0 28 28" fill="none" stroke="#fff" stroke-width="2">
            <circle cx="9" cy="9" r="3.5"/><circle cx="19" cy="9" r="3.5"/><path d="M3 22c0-4 3-6 6-6s6 2 6 6M13 22c0-4 3-6 6-6s6 2 6 6"/>
          </svg>
        </div>Transfer Students
      </div>
      <div class="service">
        <div class="service-icon">
          <svg width="28" height="28" viewBox="0 0 28 28" fill="none" stroke="#fff" stroke-width="2">
            <path d="M2 11 L14 5 L26 11 L14 17 Z"/><path d="M7 14v6c3 3 11 3 14 0v-6M24 12v7"/>
          </svg>
        </div>Graduate Students
      </div>
    </div>
    <div class="front-strip"></div>
  </section>

</main>
</body>
</html>
```